Pet sitting Business needs a website

We need a website that shows our services and prices. Shows our love of animals but also our professionalism. want a gallery, about, blog, services, links to fb and instagram accounts, newsletter archive. want it to be easy to access and wonderful to navigate. want the domain to be Birchfordpawhaven.com
take any info from FB site www.facebook.com/birchfordpawhaven
I would like it to fit square space platform

Target Market(s)

upscale area, responsible pet owners,

Industry/Entity Type

Pet Care

Coding

Coded - Design and coding required

Number of Pages Required

5+ page

Font styles to use
Sans Serif

Requirements
Must have
• (square space platform)
• Menu
• photo gallery
• about us
• services
• policies
• monthly newsletter
• unavailable dates
• Introduction (welcome)
• payment methods
• Daily updates
• testimonials (use from fb site)
Should not have
• stock photos

```html
<!DOCTYPE html>
<html lang="en">
<head>
<meta charset="utf-8">
<title>Birchford Paw Haven — Pet Sitting</title>
<link href="https://fonts.googleapis.com/css2?family=Open+Sans:wght@400;600;700;800&display=swap" rel="stylesheet">
<style>
:root{
  --blue:#137cad;
  --blue-card:#0f79a6;
  --blue-light:#3aa3d8;
  --yellow:#f4b11c;
  --ink:#2b2b2b;
  --muted:#555;
  --dark:#1d1d1d;
  --footer:#111;
  --white:#fff;
  --grey:#ececec;
}
*{box-sizing:border-box;margin:0;padding:0}
html,body{width:1200px;height:3564px;overflow:hidden}
body{font-family:"Open Sans",Arial,sans-serif;color:var(--ink);background:var(--white);position:relative}
section,footer{position:absolute;left:0;width:1200px;overflow:hidden}
.abs{position:absolute}
.photo{position:absolute}
.btn{position:absolute;display:flex;align-items:center;justify-content:center;background:var(--blue);color:var(--white);font-weight:700;font-size:12px;letter-spacing:.5px;border-radius:20px;text-transform:uppercase}
.dots{position:absolute;display:flex;gap:10px;left:50%;transform:translateX(-50%)}
.dots span{width:10px;height:10px;border-radius:50%;border:2px solid var(--white)}
.section-title{position:absolute;left:0;width:100%;text-align:center;font-size:29px;font-weight:400}

/* hero */
.hero{top:0;height:590px;background:#222}
.hero-bg{inset:0;background:radial-gradient(ellipse at 70% 40%,#7b7b7b 0%,#3c3c3c 45%,#141414 100%)}
.hero-shade{position:absolute;inset:0;background:rgba(0,0,0,.35)}
.menu-icon{position:absolute;left:1030px;top:34px}
.brand{position:absolute;top:205px;left:0;width:100%;display:flex;justify-content:center;align-items:center;gap:12px}
.brand-mark{width:34px;height:34px;border-radius:50%;background:var(--yellow)}
.brand-name{font-size:34px;font-weight:600;color:var(--yellow)}
.hero-lead{position:absolute;top:308px;left:300px;width:600px;text-align:center;color:var(--white);font-size:18.5px;line-height:26px}
.hero-sub{position:absolute;top:397px;left:320px;width:560px;text-align:center;color:var(--white);font-size:11px;line-height:17px}
.hero .btn{top:470px;left:505px;width:190px;height:38px}

/* call strip */
.call{top:590px;height:182px;background:var(--white);text-align:center}
.call-label{position:absolute;top:28px;width:100%;font-size:15px;font-weight:700;color:#333}
.call-phone{position:absolute;top:54px;width:100%;display:flex;justify-content:center;align-items:center;gap:14px;color:var(--blue);font-size:28px;font-weight:700}
.call-mail{position:absolute;top:108px;left:452px;width:296px;height:36px;border-radius:18px;background:var(--yellow);color:var(--white);font-size:13px;display:flex;align-items:center;justify-content:center;gap:12px;box-shadow:0 2px 3px rgba(0,0,0,.2)}

/* gallery */
.gallery{top:772px;height:404px}
.gallery-bg{inset:0;background:linear-gradient(180deg,#3b3f2a 0%,#2a2c1e 60%,#1f2016 100%)}
.gallery .section-title{top:16px;color:var(--white)}
.g{position:absolute;border:2px solid var(--white)}

/* about */
.about{top:1176px;height:369px;background:var(--white)}
.about h2{position:absolute;left:131px;top:10px;font-size:27px;font-weight:400}
.about-photo{left:131px;top:64px;width:166px;height:202px;border:3px solid #ddd;background:linear-gradient(160deg,#7a5a44,#3d2b20)}
.about-text{position:absolute;left:321px;top:60px;width:416px;font-size:10.5px;line-height:17px;color:var(--muted)}
.about .btn{left:318px;top:232px;width:112px;height:32px;font-size:11px}
.testimonial{position:absolute;left:765px;top:24px;width:296px;height:286px}
.testimonial h3{position:absolute;left:30px;top:28px;font-size:25px;font-weight:400}
.testimonial p{position:absolute;left:30px;top:84px;width:225px;font-size:10px;line-height:16px;color:var(--muted)}
.testimonial .avatar{position:absolute;left:30px;top:196px;width:58px;height:58px;border-radius:50%;border:3px solid var(--white);background:linear-gradient(160deg,#b17a5a,#5a3526)}
.testimonial .who{position:absolute;left:100px;top:206px;font-size:15px;color:#666}
.testimonial .who small{display:block;font-size:10px;font-style:italic}

/* services */
.services{top:1545px;height:403px}
.services-bg{inset:0;background:linear-gradient(180deg,#2c2a24 0%,#4a3e30 50%,#2a261f 100%)}
.services .section-title{top:40px;color:var(--white)}
.card{position:absolute;top:99px;width:226px;height:228px;background:var(--blue-card);color:var(--white);text-align:center}
.card h3{margin-top:18px;font-size:29px;font-weight:400}
.card .price{font-size:30px;font-weight:700;margin-top:4px}
.card .unit{font-size:10px;font-style:italic;margin-top:-4px}
.card ul{list-style:none;margin-top:16px;font-size:10px;line-height:17px;font-style:italic}
.arrows{position:absolute;top:352px;left:572px;display:flex;gap:16px}

/* policies */
.policies{top:1948px;height:463px;background:var(--white)}
.policies .section-title{top:12px}
.policy{position:absolute;left:0;width:1200px}
.policy dt{position:absolute;right:813px;width:230px;text-align:right;font-size:18px;line-height:20px}
.policy dd{position:absolute;left:416px;width:630px;font-size:10.5px;line-height:16px;font-style:italic;color:var(--muted)}
.no-refunds{position:absolute;top:348px;width:100%;text-align:center;font-size:19px;font-weight:700}
.policies .btn{left:545px;top:387px;width:112px;height:32px;font-size:11px}

/* newsletter */
.newsletter{top:2411px;height:245px}
.newsletter-bg{inset:0;background:linear-gradient(90deg,#2d2f23 0%,#4b4a38 55%,#7a6c58 80%,#a28d76 100%)}
.newsletter h2{position:absolute;left:205px;top:90px;color:var(--white);font-size:32px;font-weight:800;letter-spacing:.5px}
.newsletter p{position:absolute;left:320px;top:134px;color:var(--white);font-size:11px}
.nl-input{position:absolute;left:613px;top:95px;width:278px;height:40px;background:var(--white);font-size:11px;font-weight:700;padding-left:14px;display:flex;align-items:center}
.nl-btn{position:absolute;left:889px;top:95px;width:108px;height:40px;background:var(--yellow);color:var(--white);font-size:12px;font-weight:700;display:flex;align-items:center;justify-content:center;border-radius:0 20px 20px 0}

/* news */
.news{top:2656px;height:444px;background:var(--white)}
.news .section-title{top:22px}
.post{position:absolute;top:83px;width:226px}
.post .photo{position:relative;width:226px;height:183px;border:3px solid #ddd}
.post .date{font-size:8px;color:#777;margin-top:4px}
.post h4{font-size:12px;font-weight:800;line-height:14px;margin-top:2px}
.post p{font-size:9px;line-height:13px;color:var(--muted);margin-top:6px}
.post .more{font-size:10px;margin-top:10px;color:#333}
.post .more.accent{color:var(--yellow)}

/* contact */
.contact{top:3100px;height:416px}
.contact-bg{inset:0;background:linear-gradient(180deg,#1e1b18 0%,#2a241e 60%,#1a1714 100%)}
.contact h2{position:absolute;top:22px;width:100%;text-align:center;color:var(--white);font-size:26px;font-weight:700}
.contact .lead{position:absolute;top:64px;width:100%;text-align:center;color:var(--white);font-size:14px}
.field{position:absolute;left:238px;width:273px;height:34px;background:var(--white);font-size:10px;font-weight:600;padding:11px 10px}
.submit{position:absolute;left:238px;top:340px;width:273px;height:36px;background:var(--blue);color:var(--white);border-radius:18px;font-size:17px;display:flex;align-items:center;justify-content:center}
.col-head{position:absolute;top:134px;color:var(--blue-light);font-size:19px}
.addr{position:absolute;left:594px;color:var(--white);font-size:11px;line-height:17px;display:flex;gap:12px}
.dates{position:absolute;left:820px;top:170px;color:var(--white);font-size:15px;line-height:20px}
.callout{position:absolute;left:594px;top:312px;width:450px;color:var(--white);font-size:17px;line-height:28px}
.callout b{color:var(--blue-light);font-size:27px;font-weight:400}

/* footer */
.site-footer{top:3516px;height:48px;background:var(--footer);color:var(--white);font-size:11px}
.site-footer nav{position:absolute;left:143px;top:17px;display:flex;gap:28px}
.site-footer .copy{position:absolute;right:143px;top:17px;font-size:10px}
</style>
</head>
<body>

<section class="hero">
  <div class="photo hero-bg" role="img" aria-label="Black and white close-up of a fluffy dog"></div>
  <div class="hero-shade"></div>
  <svg class="menu-icon" width="22" height="18" viewBox="0 0 22 18"><g fill="#f4b11c"><rect y="0" width="22" height="3"/><rect y="7" width="22" height="3"/><rect y="14" width="22" height="3"/></g></svg>
  <div class="brand"><span class="brand-mark"></span><span class="brand-name">Birchford Paw Haven</span></div>
  <p class="hero-lead">The biggest key is to make people aware that I was a Licensed Veterinarian Technician from Nashville, Tn. That is a huge “selling” point when hiring someone to care for your pets</p>
  <p class="hero-sub">Instead of feeling guilty when you must leave your pet for long work days, travel or appointments you can feel good knowing that you have provided your pet with a best friend, Birchford Paw Haven.</p>
  <div class="btn">Join the club today</div>
  <div class="dots" style="top:548px"><span></span><span></span><span></span><span></span></div>
</section>

<section class="call">
  <p class="call-label">GIVE US A CALL, OR SEND US AN E-MAIL TODAY FOR A FREE CONSULTATION!</p>
  <div class="call-phone">
    <svg width="28" height="28" viewBox="0 0 28 28"><circle cx="14" cy="14" r="12" fill="none" stroke="#2a9d8f" stroke-width="2.5"/><path d="M9 9c0 6 4 10 10 10l1.5-2.5-3-1.5-1.3 1.3c-2-.8-3.7-2.5-4.5-4.5L13 10.5 11.5 7.5z" fill="#2a9d8f"/></svg>
    <span>210-555-0148</span>
  </div>
  <div class="call-mail">
    <svg width="14" height="11" viewBox="0 0 14 11"><rect x=".5" y=".5" width="13" height="10" fill="none" stroke="#fff"/><path d="M.5.5l6.5 5 6.5-5" fill="none" stroke="#fff"/></svg>
    <span>birchfordpawhaven@gmail.com</span>
  </div>
</section>

<section class="gallery">
  <div class="photo gallery-bg" role="img" aria-label="Blurred outdoor grass background"></div>
  <h2 class="section-title">Photo Gallery</h2>
  <div class="g" style="left:131px;top:71px;width:285px;height:274px;background:linear-gradient(150deg,#8a6a55,#4a3a30)" role="img" aria-label="Smiling girl holding a grey cat"></div>
  <div class="g" style="left:428px;top:71px;width:142px;height:134px;background:linear-gradient(150deg,#c9a47a,#8a6848)" role="img" aria-label="Small fluffy puppy"></div>
  <div class="g" style="left:428px;top:211px;width:142px;height:134px;background:linear-gradient(150deg,#9a9a9a,#3c3c3c)" role="img" aria-label="Black and white puppy"></div>
  <div class="g" style="left:582px;top:71px;width:195px;height:274px;background:linear-gradient(150deg,#7a7a7a,#2d2d2d)" role="img" aria-label="Black and white photo of two girls"></div>
  <div class="g" style="left:789px;top:71px;width:280px;height:134px;background:linear-gradient(150deg,#6f8a5a,#3b4c30)" role="img" aria-label="Dogs playing on a lawn"></div>
  <div class="g" style="left:789px;top:211px;width:280px;height:134px;background:linear-gradient(150deg,#7a6a80,#3a3048)" role="img" aria-label="Girls posing with a pet"></div>
  <div class="dots" style="top:381px;gap:8px"><span style="width:6px;height:6px;border:0;background:#f4b11c"></span><span style="width:6px;height:6px;border:0;background:#fff"></span><span style="width:6px;height:6px;border:0;background:#fff"></span></div>
</section>

<section class="about">
  <h2>About Us</h2>
  <div class="photo about-photo" role="img" aria-label="Portrait of the owner with her dog"></div>
  <p class="about-text">Hi my name is Dana Whitcombe and I would love to introduce myself. I am a Licensed Veterinarian Technician from Nashville, Tennessee. My family and I moved to San Antonio in 2008. I have dedicated the last 13 years to raising my 2 beautiful children and 5 of my furry babies. I have the knowledge and the training to give the special care your pet will need. I was a Licensed Veterinarian Technician Supervisor of a major animal hospital in Nashville. I have spent 20 years of my life taking care of our friends and would love to do the same for yours.</p>
  <div class="btn">Read more</div>
  <div class="testimonial">
    <svg class="abs" style="left:0;top:0" width="296" height="300" viewBox="0 0 296 300"><path d="M20 0h256a20 20 0 0 1 20 20v246a20 20 0 0 1-20 20h-40l24 14-52-14H20A20 20 0 0 1 0 266V20A20 20 0 0 1 20 0z" fill="#ececec"/></svg>
    <h3>Testimonials</h3>
    <p>Duis aute irure dolor in reprehenderit in voluptate velit esse cillum dolore eu fugiat nulla pariatur. Excepteur sint occaecat cupidatat non proident, sunt in culpa qui officia deserunt mollit anim id est laborum.</p>
    <div class="avatar" role="img" aria-label="Client portrait"></div>
    <div class="who">Marla Quinn<small>Happy client</small></div>
  </div>
</section>

<section class="services">
  <div class="photo services-bg" role="img" aria-label="Blurred photo of a dog outdoors"></div>
  <h2 class="section-title">Services</h2>
  <div class="card" style="left:131px"><h3>Daily Visit</h3><div class="price">$25.00</div><div class="unit">per visit</div><ul><li>No additional charge for each pet</li><li>Dog walks or play time for your pet</li><li>Feeding and fresh water</li><li>Cleaning up any “accidents”, litter boxes, cages</li></ul></div>
  <div class="card" style="left:369px"><h3>Potty visits</h3><div class="price">$10.00</div><div class="unit">&nbsp;</div><ul><li>Usually done at noon and bedtime</li><li>letting them out to potty</li><li>some playtime (noon time only)</li><li>checking surroundings</li></ul></div>
  <div class="card" style="left:606px"><h3>Dog park</h3><div class="price">$40.00</div><div class="unit">20 min to play</div><ul><li>must be scheduled week in advance</li></ul></div>
  <div class="card" style="left:843px"><h3>Just walks</h3><div class="price">$15.00</div><div class="unit">20 min walk</div><ul><li>No additional charge for each pet</li><li>Dog walks or play time for your pet</li><li>Feeding and fresh water</li><li>Cleaning up any “accidents”, litter boxes, cages</li></ul></div>
  <div class="arrows"><svg width="14" height="26" viewBox="0 0 14 26"><path d="M12 2L2 13l10 11" fill="none" stroke="#ccc" stroke-width="2"/></svg><svg width="14" height="26" viewBox="0 0 14 26"><path d="M2 2l10 11L2 24" fill="none" stroke="#ccc" stroke-width="2"/></svg></div>
</section>

<section class="policies">
  <h2 class="section-title">Policies</h2>
  <dl>
    <div class="policy" style="top:86px"><dt>Consultation visit</dt><dd>You will receive a free visit consultation from Birchford Paw Haven to meet you and your pet. During this visit we will discuss all important issues with you and can help you fill out the necessary documents. This is the time to provide Birchford Paw Haven with a key to your house, or a garage door opener and any security alarm codes.</dd></div>
    <div class="policy" style="top:160px"><dt>Vaccinations</dt><dd>If participating in the dog park or other venues where they may be in contact with other animals (grooming/daycare, vet taxi) a copy of current vaccinations is required.</dd></div>
    <div class="policy" style="top:218px"><dt>Dog Park</dt><dd>Dogs must get along with other dogs. Respond to voice command. No more than 2 dogs per household can attend dog park at one time. Owners will have to sign a liability form before the pets are allowed to go.</dd></div>
    <div class="policy" style="top:276px"><dt>Cancellations<br>and Early Returns</dt><dd>Life happens and things get cancelled. We do not penalize you for cancellations. Early returns we do retain all fees as original booked.</dd></div>
  </dl>
  <p class="no-refunds">NO REFUNDS FOR HOLIDAY CANCELLATIONS!</p>
  <div class="btn">Read more</div>
</section>

<section class="newsletter">
  <div class="photo newsletter-bg" role="img" aria-label="Woman hugging a small white dog outdoors"></div>
  <h2>JOIN OUR NEWSLETTER</h2>
  <p>For Happy Hours to spend time to your pets</p>
  <div class="nl-input">Enter Email Id</div>
  <div class="nl-btn">Subscribe</div>
</section>

<section class="news">
  <h2 class="section-title">News</h2>
  <article class="post" style="left:131px"><div class="photo" style="background:linear-gradient(150deg,#b89a84,#6a5446)" role="img" aria-label="Girl with a small dog on a couch"></div><p class="date">Post on - 12 Aug 2016</p><h4>NEQUE PORRO QUISQUAM EST QUI DOLOREM IPSUM...</h4><p>Excepteur sint occaecat cupidatat non proident, sunt in culpa qui officia deserunt mollit anim id est laborum.</p><p class="more accent">Read more ›</p></article>
  <article class="post" style="left:369px"><div class="photo" style="background:linear-gradient(150deg,#6a5a4c,#1e1a16)" role="img" aria-label="Girl with a black dog"></div><p class="date">Post on - 12 Aug 2016</p><h4>NEQUE PORRO QUISQUAM EST QUI DOLOREM IPSUM...</h4><p>Excepteur sint occaecat cupidatat non proident, sunt in culpa qui officia deserunt mollit anim id est laborum.</p><p class="more">Read more ›</p></article>
  <article class="post" style="left:606px"><div class="photo" style="background:linear-gradient(150deg,#8aa070,#4a5a3a)" role="img" aria-label="Girl holding a pug outdoors"></div><p class="date">Post on - 12 Aug 2016</p><h4>NEQUE PORRO QUISQUAM EST QUI DOLOREM IPSUM...</h4><p>Excepteur sint occaecat cupidatat non proident, sunt in culpa qui officia deserunt mollit anim id est laborum.</p><p class="more">Read more ›</p></article>
  <article class="post" style="left:843px"><div class="photo" style="background:linear-gradient(150deg,#a89080,#5a4438)" role="img" aria-label="Girl with a cat on a porch"></div><p class="date">Post on - 12 Aug 2016</p><h4>NEQUE PORRO QUISQUAM EST QUI DOLOREM IPSUM...</h4><p>Excepteur sint occaecat cupidatat non proident, sunt in culpa qui officia deserunt mollit anim id est laborum.</p><p class="more">Read more ›</p></article>
</section>

<section class="contact">
  <div class="photo contact-bg" role="img" aria-label="Dark blurred photo of a dog"></div>
  <h2>Contact Us Today</h2>
  <p class="lead">Please fill out the form below, and we will contact you.</p>
  <div class="field" style="top:124px">Name</div>
  <div class="field" style="top:164px">Email</div>
  <div class="field" style="top:204px">Address</div>
  <div class="field" style="top:244px;height:86px">Message</div>
  <div class="submit">SUBMIT</div>
  <h3 class="col-head" style="left:594px">ADDRESS</h3>
  <div class="addr" style="top:174px"><svg width="10" height="14" viewBox="0 0 10 14"><path d="M5 0a5 5 0 0 0-5 5c0 4 5 9 5 9s5-5 5-9a5 5 0 0 0-5-5z" fill="#fff"/><circle cx="5" cy="5" r="2" fill="#2a241e"/></svg><span>Main Store 418 Larkspur Rd<br>South Houston</span></div>
  <div class="addr" style="top:230px"><svg width="12" height="12" viewBox="0 0 12 12"><path d="M2 1l2.5 0 1 3-1.5 1a6 6 0 0 0 3 3l1-1.5 3 1V10a1 1 0 0 1-1 1A10 10 0 0 1 1 2a1 1 0 0 1 1-1z" fill="#fff"/></svg><span>77587 (346) 555-0192</span></div>
  <div class="addr" style="top:258px"><svg width="12" height="10" viewBox="0 0 12 10"><rect width="12" height="10" fill="#fff"/><path d="M0 0l6 5 6-5" fill="none" stroke="#2a241e"/></svg><span>info@birchfordpawhaven.com</span></div>
  <h3 class="col-head" style="left:820px">NOT AVAILABLE</h3>
  <div class="dates">Unavailable dates<br><br>May 6-8th<br>MAY 21-23<br>July 3-16</div>
  <p class="callout">IF YOU WOULD RATHER CALL, YOU CAN REACH US AT <b>210-555-0148</b></p>
</section>

<footer class="site-footer">
  <nav><span>Home</span><span>Photo Gallery</span><span>About Us</span><span>Services</span><span>Policies</span><span>Monthly newsletter</span><span>Contact Us</span></nav>
  <p class="copy">© All rights reserved 2016. www.birchfordpawhaven.com</p>
</footer>

</body>
</html>
```